Brookvale Estates LLC stationary for a real estate property management company.

Create stationary (letterhead, envelopes, business cards) using Brookvale Estates LLC logo as primary creative element. Stationary design needs to be horizontal, leaving as much space as possible for correspondence copy. See attached Creative Brief and past stationary files for details.

Target Market(s)

Prospective apartment residents and current residents, vendors, and government agencies.

Industry/Entity Type

Property Management

Contact Information for Business Card

Business card employee title: Property Manager. Should include address, phone, fax, email, website, slogan, and Brookvale Estates logo.

Font styles to use
Sans Serif

Colors
0592cd
000000

Requirements
Must have
• Tone should be conservative, institutional, business (i.e. banking, finance, real estate). Must include: address, phone, fax, website, and slogan (see attached Creative Brief). Should be a horizontal design, leaving as much room as possible for letter correspondence copy.
Nice to have
• Please use an Arial or Helvetica style font.
Should not have
• Letterhead layout should leave as much room as possible for copy.

```html
<!DOCTYPE html>
<html lang="en">
<head>
<meta charset="utf-8">
<title>Brookvale Estates LLC – Business Cards</title>
<link href="https://fonts.googleapis.com/css2?family=Arimo:ital,wght@0,400;0,700;1,700&display=swap" rel="stylesheet">
<style>
  :root {
    --brand-blue: #0a6aab;
    --brand-cyan: #0592cd;
    --ink: #3a3a3a;
    --ink-soft: #4d4d4d;
    --card-white: #f4f4f4;
    --slate-light: #6c6c6e;
    --slate-dark: #464648;
    --stage: #262626;
    --label: #ffffff;
  }
  * { box-sizing: border-box; margin: 0; padding: 0; }
  html, body { width: 1200px; height: 793px; overflow: hidden; }
  body {
    background: var(--stage);
    font-family: "Arimo", Arial, sans-serif;
    position: relative;
  }
  .card {
    position: absolute;
    width: 497px;
    height: 283px;
    overflow: hidden;
  }
  .card--front { left: 91px; top: 88px; background: var(--card-white); }
  .card--back-light { left: 622px; top: 88px; background: linear-gradient(135deg, #f8f8f8, #ececec); }
  .card--back-dark { left: 91px; top: 424px; background: linear-gradient(135deg, var(--slate-light), var(--slate-dark) 55%); }
  .card--back-band { left: 622px; top: 425px; background: linear-gradient(135deg, var(--slate-light), var(--slate-dark) 55%); }

  .card-label {
    position: absolute;
    font-style: italic;
    font-weight: 700;
    font-size: 11px;
    color: var(--label);
    text-align: center;
    width: 200px;
  }
  .label-front { left: 223px; top: 389px; }
  .label-back1 { left: 776px; top: 389px; }
  .label-back2 { left: 224px; top: 729px; }
  .label-back3 { left: 793px; top: 729px; }

  .front-accent { position: absolute; left: 0; top: 0; }

  .front-info {
    position: absolute;
    right: 21px;
    top: 30px;
    text-align: right;
    color: var(--ink-soft);
  }
  .company-name {
    color: var(--brand-blue);
    font-weight: 700;
    font-size: 29px;
    line-height: 1;
    letter-spacing: 0.5px;
  }
  .company-name span { display: block; }
  .person-name {
    margin-top: 14px;
    color: var(--brand-blue);
    font-weight: 700;
    font-size: 17px;
    line-height: 1.1;
  }
  .person-title { font-size: 13px; margin-top: 2px; color: var(--ink); }
  .address { margin-top: 12px; font-size: 12px; line-height: 15px; }
  .contact { margin-top: 12px; font-size: 12px; line-height: 16px; }

  .faint-circle { position: absolute; }

  .back-lockup {
    position: absolute;
    right: 33px;
    top: 170px;
    display: flex;
    align-items: center;
    gap: 10px;
  }
  .back-lockup .dot {
    width: 40px; height: 40px;
    border: 3px solid #ffffff;
    border-radius: 50%;
  }
  .back-lockup .name {
    color: #ffffff;
    font-weight: 700;
    font-size: 21px;
    line-height: 1.05;
  }
  .slogan {
    position: absolute;
    color: #ffffff;
    font-weight: 700;
    font-size: 12.5px;
  }
  .slogan--lockup { right: 34px; top: 245px; }

  .slogan-band {
    position: absolute;
    left: 0; right: 0;
    top: 247px;
    height: 24px;
    background: linear-gradient(90deg, #1d7fbc, #1664a0);
    display: flex;
    align-items: center;
    justify-content: center;
  }
  .slogan-band .slogan { position: static; }
</style>
</head>
<body>

  <section class="card card--front" aria-label="Business card front">
    <svg class="front-accent" width="497" height="283" viewBox="0 0 497 283">
      <defs>
        <linearGradient id="frontBlue" x1="0" y1="0" x2="0" y2="1">
          <stop offset="0" stop-color="#17b8ec"/>
          <stop offset="1" stop-color="#0592cd"/>
        </linearGradient>
      </defs>
      <rect x="0" y="0" width="120" height="283" fill="url(#frontBlue)"/>
      <circle cx="210" cy="170" r="186" fill="var(--card-white)"/>
    </svg>
    <div class="front-info">
      <div class="company-name"><span>BROOKVALE</span><span>ESTATES LLC</span></div>
      <div class="person-name">DANA WHITFIELD</div>
      <div class="person-title">Property Manager</div>
      <div class="address">2780 Larkspur Ridge Drive #B210<br>Fairhaven, CA 90412</div>
      <div class="contact">Phone: 555-318-2047<br>Fax: 555-318-2090<br>dana@brookvaleestates.us<br>www.brookvaleestates.us</div>
    </div>
  </section>
  <div class="card-label label-front">FRONT CARD</div>

  <section class="card card--back-light" aria-label="Business card back, light version">
    <svg class="faint-circle" width="497" height="283" viewBox="0 0 497 283">
      <circle cx="250" cy="150" r="128" fill="none" stroke="#e2e2e2" stroke-width="6"/>
    </svg>
  </section>
  <div class="card-label label-back1">BACK CARD_01</div>

  <section class="card card--back-dark" aria-label="Business card back, dark version">
    <div class="back-lockup">
      <div class="dot"></div>
      <div class="name">BROOKVALE<br>ESTATES LLC</div>
    </div>
    <div class="slogan slogan--lockup">Multifamily Property Management</div>
  </section>
  <div class="card-label label-back2">BACK CARD_02</div>

  <section class="card card--back-band" aria-label="Business card back, band version">
    <svg class="faint-circle" width="497" height="283" viewBox="0 0 497 283">
      <circle cx="260" cy="140" r="122" fill="none" stroke="#6a6a6c" stroke-width="6"/>
    </svg>
    <div class="slogan-band"><span class="slogan">Multifamily Property Management</span></div>
  </section>
  <div class="card-label label-back3">BACK CARD_03</div>

</body>
</html>
```